Healthcare and Professional IT Services Company need a redesigned business card

We are a IT Services company that targets small medical practices and professional business such as Attorneys, Accounts, Architects etc. We want to communicate a professional yet friendly image using recent logo redesign here on ArtHarbor. Like to see the colors blue and orange in the design. Must use the Tall Pine Computing as displayed in the new logo - then also want to incorporate the fish logo as well.

Target Market(s)

Small medical and professional services

Industry/Entity Type

It Company

Contact Information for Business Card

The usual stuff, place for name address phone website. Also maybe our tagline which is "hooked on technology"

Requirements
Must have
• My new logo and the fish somewhere on the card

```html
<!DOCTYPE html>
<html lang="en">
<head>
<meta charset="utf-8">
<title>Tall Pine Computing – Business Card</title>
<link href="https://fonts.googleapis.com/css2?family=Open+Sans:wght@400;600&display=swap" rel="stylesheet">
<style>
  :root {
    --page-bg: #e9e7e3;
    --card-white: #fbfbfa;
    --band-dark: #2f3435;
    --band-blue-light: #2cb2e2;
    --band-blue-deep: #1477b6;
    --brand-blue: #35b4e4;
    --text-dark: #1f2324;
    --divider: #3a3f40;
  }
  * { margin: 0; padding: 0; box-sizing: border-box; }
  html, body {
    width: 1200px; height: 892px; overflow: hidden;
    background: var(--page-bg);
    font-family: "Open Sans", sans-serif;
  }
  .canvas {
    width: 1200px; height: 892px;
    display: flex; align-items: center; justify-content: center; gap: 48px;
  }
  .card {
    width: 540px; height: 309px;
    background: var(--card-white);
    position: relative; overflow: hidden;
    box-shadow: 0 6px 18px rgba(0,0,0,.18);
  }
  /* Front */
  .band-top { position: absolute; left: 0; top: 0; width: 100%; height: 66px; background: var(--band-dark); }
  .band-bottom {
    position: absolute; left: 0; bottom: 0; width: 100%; height: 66px;
    background: linear-gradient(90deg, var(--band-blue-light), var(--band-blue-deep));
  }
  .brand {
    position: absolute; left: 160px; top: 92px;
    display: flex; align-items: center; gap: 8px;
    color: var(--brand-blue); font-weight: 600; font-size: 21px; letter-spacing: .2px;
  }
  .brand-dot { width: 14px; height: 14px; border-radius: 50%; background: var(--brand-blue); }
  .holder {
    position: absolute; left: 34px; top: 180px;
    font-size: 25px; font-weight: 400; letter-spacing: 1.5px; color: var(--text-dark);
  }
  .divider { position: absolute; left: 252px; top: 148px; width: 1px; height: 76px; background: var(--divider); }
  .contacts {
    position: absolute; left: 266px; top: 146px;
    list-style: none; font-size: 13.5px; font-weight: 600; color: var(--text-dark);
    letter-spacing: .6px; line-height: 19px;
  }
  .contacts li { display: flex; align-items: center; gap: 6px; }
  .icon { width: 12px; height: 12px; flex: none; }
  .contacts .indent { padding-left: 18px; }
  /* Back */
  .card-back { background: linear-gradient(135deg, #ffffff, #eeeeee); }
  .back-brand {
    position: absolute; inset: 0;
    display: flex; align-items: center; justify-content: center; gap: 12px;
    color: var(--brand-blue); font-weight: 600; font-size: 34px;
  }
  .back-brand .brand-dot { width: 22px; height: 22px; }
</style>
</head>
<body>
<main class="canvas">
  <section class="card card-front" aria-label="Business card front">
    <div class="band-top"></div>
    <div class="brand"><span class="brand-dot"></span>Tall Pine Computing</div>
    <p class="holder">Daniel Hartley</p>
    <div class="divider"></div>
    <ul class="contacts">
      <li>
        <svg class="icon" viewBox="0 0 12 12"><rect width="12" height="12" fill="#1f2324"/><path d="M3 2.5 L4.6 2.5 L5.2 4.4 L4.3 5.1 Q5.2 7 6.9 7.7 L7.6 6.8 L9.5 7.4 L9.5 9 Q5.5 9.5 3 4.5 Z" fill="#fff"/></svg>
        0412 555019
      </li>
      <li>
        <svg class="icon" viewBox="0 0 12 12"><rect width="12" height="12" fill="#1f2324"/><circle cx="6" cy="6" r="3.6" fill="none" stroke="#fff" stroke-width="1"/><path d="M2.4 6 H9.6 M6 2.4 V9.6" stroke="#fff" stroke-width=".8"/></svg>
        www.tallpine.com
      </li>
      <li>
        <svg class="icon" viewBox="0 0 12 12"><rect width="12" height="12" fill="#1f2324"/><path d="M6 10 L3.5 5.8 A2.8 2.8 0 1 1 8.5 5.8 Z" fill="#fff"/><circle cx="6" cy="4.6" r="1" fill="#1f2324"/></svg>
        2480 Harbor Crest Way
      </li>
      <li class="indent">Bay Meadow, CA 94000</li>
    </ul>
    <div class="band-bottom"></div>
  </section>

  <section class="card card-back" aria-label="Business card back">
    <div class="back-brand"><span class="brand-dot"></span>Tall Pine Computing</div>
  </section>
</main>
</body>
</html>
```